bRu Design Group - architect web site

need a web site to permit potential clients to view our portfolio of work.

Will need lots of photos included.

Industry/Entity Type

Architect

Coding

Coded - Design and coding required

Number of Pages Required

5+ page

Font styles to use
Sans Serif

Requirements
Must have
• photos should be organized by project - perhaps a summary of photos and then click to enlarge? should be simple to operate. should be able to separate interior design from architecture.
• needs to be easy to add more photos in the future.

```html
<!DOCTYPE html>
<html lang="en">
<head>
<meta charset="utf-8">
<title>bRu Design Group – Architecture &amp; Interiors</title>
<link href="https://fonts.googleapis.com/css2?family=Open+Sans:wght@400;600;700&display=swap" rel="stylesheet">
<style>
:root{
  --ink:#2b2b2b;
  --muted:#8a8a8a;
  --line:#d6d9dc;
  --header:rgba(70,68,80,.78);
  --features-bg:#f1f5f8;
  --accent:#a9c3c8;
  --caption:rgba(118,150,150,.85);
  --facts-bg:#2f3136;
  --map-bg:#e6e7e8;
  --footer-bg:#4c4b5e;
  --footer-text:#d9d8e2;
  --white:#fff;
}
*{box-sizing:border-box;margin:0;padding:0}
html,body{width:1200px;height:3396px;overflow:hidden}
body{font-family:"Open Sans",Arial,sans-serif;color:var(--ink);background:var(--white);position:relative}
.abs{position:absolute}
section,header,footer{position:absolute;left:0;width:1200px}

/* header + hero */
.hero{top:0;height:675px;background:linear-gradient(180deg,#c9c6c0 0%,#b9ad9c 55%,#8f7d66 100%)}
.site-header{top:0;height:100px;background:var(--header);z-index:2}
.brand{left:90px;top:34px;color:var(--white);font-weight:700;font-size:22px;letter-spacing:.5px}
.main-nav{left:385px;top:38px;display:flex;gap:0;font-size:13px;color:var(--white)}
.main-nav span{position:absolute;white-space:nowrap}
.social-top{left:1016px;top:42px;display:flex;gap:10px}
.social-top i{width:10px;height:10px;border-radius:50%;background:var(--white);display:block}
.nav-divider{left:988px;top:32px;width:1px;height:36px;background:rgba(255,255,255,.3)}
.hero-caption{left:97px;top:573px;width:645px;height:52px;background:var(--caption);color:var(--white);font-weight:700;font-size:15px;display:flex;align-items:center;justify-content:center;text-transform:uppercase}
.slider-arrow{top:362px;width:36px;height:36px;border-radius:50%;background:rgba(255,255,255,.55)}

/* shared */
.section-title{width:1200px;left:0;text-align:center;font-weight:700;font-size:22px;text-transform:uppercase}
.divider{left:500px;width:200px;height:14px}
.lead{width:1200px;left:0;text-align:center;font-size:15px;line-height:23px;color:#3a3a3a}

/* features */
.features{top:675px;height:394px;background:var(--features-bg)}
.feature{width:310px}
.feature-icon{left:0;top:0;width:34px;height:34px;border-radius:50%;border:1px solid var(--line);background:var(--white)}
.feature h3{position:absolute;left:45px;top:0;font-size:16px;font-weight:600}
.feature p{position:absolute;left:45px;top:30px;width:265px;font-size:11px;line-height:16px;color:var(--muted)}
.dots{left:572px;top:340px;display:flex;gap:12px}
.dots i{width:6px;height:6px;border-radius:50%;background:#d7dde1;display:block}
.dots i:first-child{background:#4a4a4a}

/* portfolio */
.portfolio{top:1069px;height:810px}
.filters{top:251px;left:0;width:1200px;font-size:12px;font-weight:600}
.filters span{position:absolute;top:0;padding:5px 0;white-space:nowrap}
.filters .active{background:var(--accent);color:var(--white);width:50px;text-align:center;border-radius:2px}
.gallery{top:301px;left:0;display:grid;grid-template-columns:250px 343px 342px 265px;grid-template-rows:256px 253px}
.tile{position:relative}
.tile-hover{background:#b4ccd0;color:var(--white);display:flex;flex-direction:column;align-items:center;justify-content:center;text-align:center}
.tile-hover h4{font-size:16px;font-weight:600;margin-top:16px}
.tile-hover small{font-size:12px;opacity:.85}
.eye{width:34px;height:34px;border-radius:50%;border:1.5px solid var(--white);display:flex;align-items:center;justify-content:center}

/* facts */
.facts{top:1879px;height:514px;background:linear-gradient(180deg,#3b3d43 0%,#2c2d31 60%,#3a3328 100%);color:var(--white)}
.fact{width:200px;text-align:center}
.fact-ring{width:112px;height:112px;margin:0 auto;border-radius:50%;border:1px solid rgba(255,255,255,.55);display:flex;align-items:center;justify-content:center}
.fact strong{display:block;font-size:46px;font-weight:400;margin-top:40px;line-height:50px}
.fact span{display:block;font-size:14px;text-transform:uppercase;margin-top:2px}

/* contact */
.contact{top:2393px;height:550px}
.contact-intro{left:91px;top:238px;width:240px}
.contact-intro h3{font-size:19px;font-weight:400;line-height:27px}
.contact-intro address{font-style:normal;font-size:11px;line-height:17px;color:var(--muted);margin-top:30px}
.form-title{left:351px;top:237px;font-size:20px;font-weight:700}
.field{border-bottom:1px solid var(--line);font-size:11px;color:var(--muted);padding-bottom:12px}
.send{left:894px;top:437px;font-size:13px;color:#555;display:flex;align-items:center;gap:10px}
.social-side{left:1056px;top:266px;display:flex;flex-direction:column;gap:16px}
.social-side i{width:18px;height:18px;border-radius:50%;background:#cfd2d5;display:block}

/* map */
.map{top:2943px;height:163px;background:linear-gradient(90deg,#e9eaeb,#dedfe1 50%,#e8e9ea)}

/* footer */
.site-footer{top:3106px;height:290px;background:var(--footer-bg);color:var(--footer-text);border-top:4px solid #3b3a4b}
.footer-col h4{font-size:14px;font-weight:600;color:var(--white)}
.footer-col p,.footer-col li{font-size:11px;line-height:18px;list-style:none}
.subscribe{width:229px;height:37px;border:1px solid rgba(255,255,255,.35)}
.copyright{top:256px;left:0;width:1200px;text-align:center;font-size:10px;color:#b5b4c2}
</style>
</head>
<body>

<header class="site-header">
  <div class="abs brand">bRu Design Group</div>
  <nav class="abs main-nav" aria-label="Main">
    <span style="left:0">Home</span>
    <span style="left:85px">About Us</span>
    <span style="left:195px">Services</span>
    <span style="left:285px">Gallery</span>
    <span style="left:375px">Testimonials</span>
    <span style="left:500px">Contact Us</span>
  </nav>
  <div class="abs nav-divider"></div>
  <div class="abs social-top"><i></i><i></i><i></i><i></i></div>
</header>

<section class="hero" role="img" aria-label="Photo of a bright dining room with a long wooden table and white chairs opening onto a garden">
  <div class="abs slider-arrow" style="left:16px"></div>
  <div class="abs slider-arrow" style="left:1144px"></div>
  <div class="abs hero-caption">Lorem ipsum dolor sit amet, consectetur adipiscing elit. Donec</div>
</section>

<section class="features">
  <h2 class="abs section-title" style="top:58px">Features</h2>
  <svg class="abs divider" style="top:99px" viewBox="0 0 200 14"><line x1="0" y1="7" x2="88" y2="7" stroke="#d6d9dc"/><line x1="112" y1="7" x2="200" y2="7" stroke="#d6d9dc"/><path d="M100 12 L95 7 A2.6 2.6 0 0 1 100 4 A2.6 2.6 0 0 1 105 7 Z" fill="none" stroke="#999"/></svg>

  <article class="abs feature" style="left:108px;top:170px">
    <div class="abs feature-icon"></div>
    <h3>Ipsum Dolor</h3>
    <p>Sed ut perspiciatis unde omnis iste natus error sit voluptatem accusantium doloremque laudantium, totam rem aperiam, eaque ipsa quae ab illo inventore</p>
  </article>
  <article class="abs feature" style="left:448px;top:170px">
    <div class="abs feature-icon"></div>
    <h3>Lorem ipsum</h3>
    <p>Sed ut perspiciatis unde omnis iste natus error sit voluptatem accusantium doloremque laudantium, totam rem aperiam, eaque ipsa quae ab illo inventore</p>
  </article>
  <article class="abs feature" style="left:792px;top:170px">
    <div class="abs feature-icon"></div>
    <h3>Contantry popilar</h3>
    <p>Sed ut perspiciatis unde omnis iste natus error sit voluptatem accusantium doloremque laudantium, totam rem aperiam, eaque ipsa quae ab illo inventore</p>
  </article>
  <div class="abs dots"><i></i><i></i><i></i></div>
</section>

<section class="portfolio">
  <h2 class="abs section-title" style="top:80px">Portfolio</h2>
  <svg class="abs divider" style="top:121px" viewBox="0 0 200 14"><line x1="0" y1="7" x2="88" y2="7" stroke="#d6d9dc"/><line x1="112" y1="7" x2="200" y2="7" stroke="#d6d9dc"/><path d="M100 12 L95 7 A2.6 2.6 0 0 1 100 4 A2.6 2.6 0 0 1 105 7 Z" fill="none" stroke="#999"/></svg>
  <p class="abs lead" style="top:160px">Sed ut perspiciatis unde omnis iste natus error sit voluptatem accusantium doloremque laudantium, totam<br>rem aperiam, eaque ipsa quae ab illo inventore</p>
  <div class="abs filters">
    <span class="active" style="left:380px">All</span>
    <span style="left:441px">Lorem ipsum</span>
    <span style="left:546px">Lorem</span>
    <span style="left:630px">Contary</span>
    <span style="left:740px">Popilar Sit</span>
  </div>
  <div class="abs gallery">
    <div class="tile" role="img" aria-label="Interior photo of a dining room with sea view" style="background:linear-gradient(135deg,#d8d3cb,#a89a86)"></div>
    <div class="tile" role="img" aria-label="Architecture photo of a steel pergola against blue sky" style="background:linear-gradient(135deg,#1e4f96,#6c8fb8 60%,#cfd4d8)"></div>
    <div class="tile tile-hover">
      <div class="eye"><svg width="18" height="12" viewBox="0 0 18 12"><path d="M1 6 Q9 -2 17 6 Q9 14 1 6Z" fill="none" stroke="#fff"/><circle cx="9" cy="6" r="2.4" fill="#fff"/></svg></div>
      <h4>Labore et dolore magnam</h4>
      <small>Architecture</small>
    </div>
    <div class="tile" role="img" aria-label="Interior photo of a bathroom with a freestanding tub" style="background:linear-gradient(135deg,#e6ddd0,#b59f84)"></div>
    <div class="tile" role="img" aria-label="Interior photo of a living room with white sofas and sea view" style="background:linear-gradient(135deg,#b7c9d3,#e2e2de)"></div>
    <div class="tile" role="img" aria-label="Interior photo of a hallway with wooden stairs" style="background:linear-gradient(135deg,#ece9e3,#a79a89)"></div>
    <div class="tile" role="img" aria-label="Interior photo of a long wooden dining table" style="background:linear-gradient(135deg,#c3c0b8,#8c7c66)"></div>
    <div class="tile" role="img" aria-label="Interior photo of a dining room with chandeliers" style="background:linear-gradient(135deg,#e2ddd4,#a89c8a)"></div>
  </div>
</section>

<section class="facts" role="img" aria-label="Night city skyline background">
  <h2 class="abs section-title" style="top:80px;color:#fff">Some fun facts</h2>
  <svg class="abs divider" style="top:120px" viewBox="0 0 200 14"><line x1="0" y1="7" x2="88" y2="7" stroke="rgba(255,255,255,.3)"/><line x1="112" y1="7" x2="200" y2="7" stroke="rgba(255,255,255,.3)"/><path d="M100 12 L95 7 A2.6 2.6 0 0 1 100 4 A2.6 2.6 0 0 1 105 7 Z" fill="none" stroke="#fff"/></svg>

  <div class="abs fact" style="left:108px;top:157px">
    <div class="fact-ring"><svg width="30" height="30" viewBox="0 0 30 30"><circle cx="15" cy="15" r="12" fill="none" stroke="#fff" stroke-width="1.6"/><path d="M15 8v7l5 3" fill="none" stroke="#fff" stroke-width="1.6"/></svg></div>
    <strong>3200</strong><span>Hours of work</span>
  </div>
  <div class="abs fact" style="left:364px;top:157px">
    <div class="fact-ring"><svg width="30" height="30" viewBox="0 0 30 30"><circle cx="15" cy="11" r="6" fill="none" stroke="#fff" stroke-width="1.6"/><path d="M5 26c1-6 5-8 10-8s9 2 10 8z" fill="none" stroke="#fff" stroke-width="1.6"/></svg></div>
    <strong>120</strong><span>Lorem ipsu,</span>
  </div>
  <div class="abs fact" style="left:620px;top:157px">
    <div class="fact-ring"><svg width="30" height="30" viewBox="0 0 30 30"><path d="M24 6c-6 0-11 4-13 10l3 3c6-2 10-7 10-13zM11 16l-4 1 -1 4 4-1M14 19l-1 4 4-1-1-4" fill="none" stroke="#fff" stroke-width="1.6"/></svg></div>
    <strong>360</strong><span>Contany popilar</span>
  </div>
  <div class="abs fact" style="left:878px;top:157px">
    <div class="fact-ring"><svg width="30" height="30" viewBox="0 0 30 30"><path d="M9 5h12v7a6 6 0 0 1-12 0zM9 8H5c0 4 2 6 4 6M21 8h4c0 4-2 6-4 6M15 18v5M10 25h10" fill="none" stroke="#fff" stroke-width="1.6"/></svg></div>
    <strong>42</strong><span>Awards won</span>
  </div>
</section>

<section class="contact">
  <h2 class="abs section-title" style="top:80px">Contact us</h2>
  <svg class="abs divider" style="top:118px" viewBox="0 0 200 14"><line x1="0" y1="7" x2="88" y2="7" stroke="#d6d9dc"/><line x1="112" y1="7" x2="200" y2="7" stroke="#d6d9dc"/><path d="M100 12 L95 7 A2.6 2.6 0 0 1 100 4 A2.6 2.6 0 0 1 105 7 Z" fill="none" stroke="#999"/></svg>
  <p class="abs lead" style="top:161px">Voluptatem accusantium doloremque laudantium, totam rem aperiam, eaque ipsa quae ab illo inventore</p>

  <div class="abs contact-intro">
    <h3>Cras at ultrices erat, sed vulputate!</h3>
    <address>1180 Harlow Street,<br>Fairview, United States.<br>(555) 0142 388<br>studio@brudesign.example<br>www.brudesign.example</address>
  </div>

  <h3 class="abs form-title">Say hello!</h3>
  <div class="abs field" style="left:351px;top:307px;width:317px">Name</div>
  <div class="abs field" style="left:690px;top:307px;width:317px">Email</div>
  <div class="abs field" style="left:351px;top:380px;width:656px">Message</div>
  <div class="abs send"><svg width="20" height="14" viewBox="0 0 20 14"><rect x="1" y="1" width="18" height="12" fill="none" stroke="#9fb8bd"/><path d="M1 1l9 7 9-7" fill="none" stroke="#9fb8bd"/></svg>Send message</div>

  <div class="abs social-side"><i></i><i></i><i></i><i></i><i></i></div>
</section>

<section class="map" role="img" aria-label="Street map showing the studio location">
  <svg class="abs" style="left:330px;top:78px" width="22" height="30" viewBox="0 0 22 30"><path d="M11 29C4 19 2 15 2 10a9 9 0 0 1 18 0c0 5-2 9-9 19z" fill="#1e1e1e"/><circle cx="11" cy="10" r="3.5" fill="#e6e7e8"/></svg>
</section>

<footer class="site-footer">
  <div class="abs footer-col" style="left:102px;top:64px;width:210px">
    <h4>About Us</h4>
    <p style="margin-top:26px">eusmod tempor incididunt ut labore et dolore magna aliqua. Ut enim ad minim veniam, quis nostrud exercitation ullamco laboris nisi ut aliquip ex ea commodo consequat.</p>
  </div>
  <div class="abs footer-col" style="left:412px;top:64px;width:240px">
    <h4>Subscribe</h4>
    <div class="subscribe" style="margin-top:28px;position:relative"><svg class="abs" style="right:10px;top:12px" width="18" height="10" viewBox="0 0 18 10"><path d="M0 5h16M12 1l4 4-4 4" fill="none" stroke="#d9d8e2"/></svg></div>
    <p style="margin-top:14px;width:200px">eusmod tempor incididunt ut labore et dolore magna aliqua.</p>
  </div>
  <div class="abs footer-col" style="left:738px;top:64px;width:260px">
    <h4>Explore</h4>
    <ul class="abs" style="left:0;top:44px;width:120px"><li>Lorem</li><li>ipsum dolor sit</li><li>amt contantry</li><li>popilar sit</li></ul>
    <ul class="abs" style="left:127px;top:44px;width:120px"><li>Contantry pop</li><li>Northfield</li><li>Brightway</li><li>Lumen</li></ul>
  </div>
  <div class="abs footer-col" style="left:1021px;top:64px;width:140px">
    <h4>Menu</h4>
    <ul style="margin-top:24px"><li>Home</li><li>How it works</li><li>Featured</li><li>Articles</li><li>Contact us</li></ul>
  </div>
  <div class="abs copyright">© 2015 brudesign. All Rights Reserved.</div>
</footer>

</body>
</html>
```